Corvane Paintless Dent Removal

Our company works on vehicles removing dents using a highly skilled trade which the metal is massaged out with special tools without disturbing the original paint, hence paintless dent removal. Besides keeping the paint and metal original its also very environmentally friendly since no paint or toxic fillers are used. Also we we are one of the most experienced companies in the business with 25 years

Target Market(s)

Retail Automobile consumers, Auto Dealerships and Auto Body Shops

Industry/Entity Type

Auto Repair

Contact Information for Business Card

Dale Hollister
PO Box 518 Brookmere, NY 11962
631-555-0148
corvanepdr@mailbox-example.com
website corvanepdr.example
youtube corvane paintless dent removal
25 years of experience removing Dents, Dings and Hail Damage

Font styles to use
Serif
Sans Serif

Colors

Designer to choose colors to be used in the design.

Requirements
Must have
• I do like things that are simple but classy and somewhat bold, also I like my logo so that should be somewhat important

```html
<!DOCTYPE html>
<html lang="en">
<head>
<meta charset="utf-8">
<title>Corvane Paintless Dent Removal – Business Card</title>
<link rel="stylesheet" href="https://fonts.googleapis.com/css2?family=Roboto:wght@400;500;700;900&display=swap">
<style>
  :root {
    --backdrop: #3a3a3c;
    --card: #232325;
    --card-edge: #1a1a1b;
    --emboss: #333336;
    --emboss-light: #3d3d40;
    --green: #7dc21e;
    --navy: #0f2a5c;
    --text: #e6e6e6;
    --muted: #cfcfcf;
  }
  * { box-sizing: border-box; margin: 0; padding: 0; }
  html, body { width: 799px; height: 1200px; overflow: hidden; }
  body {
    background: var(--backdrop);
    font-family: "Roboto", Arial, sans-serif;
    position: relative;
  }
  .card {
    position: absolute;
    left: 90px;
    width: 620px;
    height: 354px;
    background: var(--card);
    border: 1px solid var(--card-edge);
    box-shadow: 0 14px 30px rgba(0,0,0,.45);
    overflow: hidden;
  }
  .card--front { top: 140px; }
  .card--back { top: 700px; }

  /* front: blind-embossed name mark */
  .front-mark {
    position: absolute;
    inset: 0;
    display: flex;
    align-items: center;
    justify-content: center;
    gap: 18px;
  }
  .front-mark__dot {
    width: 22px; height: 22px; border-radius: 50%;
    background: var(--emboss-light);
  }
  .front-mark__name {
    font-weight: 900;
    font-size: 34px;
    line-height: 1.1;
    color: var(--emboss-light);
    text-transform: uppercase;
    letter-spacing: 1px;
    text-align: center;
  }

  /* back: name mark */
  .brand {
    position: absolute;
    left: 34px; top: 98px;
    width: 250px;
    display: flex;
    align-items: center;
    gap: 12px;
  }
  .brand__dot { flex: none; width: 16px; height: 16px; border-radius: 50%; background: var(--green); }
  .brand__name {
    font-weight: 900;
    font-size: 23px;
    line-height: 1.1;
    color: var(--green);
    text-transform: uppercase;
  }

  .contact {
    position: absolute;
    left: 340px; top: 100px;
    color: var(--text);
  }
  .contact__name { font-weight: 700; font-size: 27px; color: var(--green); }
  .contact__role { font-size: 14px; color: var(--muted); margin: 2px 0 14px; }
  .contact__address { font-size: 15px; line-height: 1.25; margin-bottom: 10px; }
  .contact__list { list-style: none; font-size: 15px; }
  .contact__list li { display: flex; align-items: center; gap: 10px; margin-bottom: 4px; }
  .contact__list svg { width: 14px; height: 14px; flex: none; }

  .footer-bands { position: absolute; left: 0; bottom: 0; width: 620px; height: 70px; }
  .video-link {
    position: absolute;
    left: 320px; bottom: 18px;
    display: flex; align-items: center; gap: 12px;
    color: #fff; font-size: 17px;
  }
  .video-link__square { width: 16px; height: 16px; background: #fff; border-radius: 3px; }
</style>
</head>
<body>
  <section class="card card--front" aria-label="Card front">
    <div class="front-mark">
      <span class="front-mark__dot"></span>
      <span class="front-mark__name">Corvane<br>Paintless Dent Removal</span>
    </div>
  </section>

  <section class="card card--back" aria-label="Card back">
    <div class="brand">
      <span class="brand__dot"></span>
      <span class="brand__name">Corvane Paintless Dent Removal</span>
    </div>

    <div class="contact">
      <h1 class="contact__name">Dale Hollister</h1>
      <p class="contact__role">Managing Director</p>
      <p class="contact__address">PO Box 518 Brookmere,<br>NY 11962</p>
      <ul class="contact__list">
        <li>
          <svg viewBox="0 0 16 16"><path fill="var(--green)" d="M3 1h3l1 4-2 1.5a9 9 0 0 0 4.5 4.5L11 9l4 1v3a2 2 0 0 1-2 2C6.5 15 1 9.5 1 3a2 2 0 0 1 2-2z"/></svg>
          631-555-0148
        </li>
        <li>
          <svg viewBox="0 0 16 16"><rect x="1" y="3" width="14" height="10" fill="var(--green)"/><path d="M1 3l7 6 7-6" fill="none" stroke="var(--card)" stroke-width="1.4"/></svg>
          corvanepdr@mailbox-example.com
        </li>
        <li>
          <svg viewBox="0 0 16 16" fill="none" stroke="var(--green)" stroke-width="1.5"><circle cx="8" cy="8" r="6.5"/><path d="M1.5 8h13M8 1.5c-3 3.5-3 9.5 0 13M8 1.5c3 3.5 3 9.5 0 13"/></svg>
          www.corvanepdr.example
        </li>
      </ul>
    </div>

    <svg class="footer-bands" viewBox="0 0 620 70" aria-hidden="true">
      <polygon points="0,6 290,46 290,52 0,12" fill="var(--green)"/>
      <polygon points="0,6 250,40 0,40" fill="none"/>
      <polygon points="255,70 300,18 620,18 620,70" fill="var(--navy)"/>
      <rect x="0" y="58" width="260" height="12" fill="var(--green)"/>
    </svg>
    <div class="video-link">
      <span class="video-link__square"></span>
      <span>videohub.example/Dale Hollister</span>
    </div>
  </section>
</body>
</html>
```